Business Card Design Project

We need a Business Card for an Mechanical Engineering firm in Singapore. The design should be Modern & Technical looking, yet eye catching.

Our company deals in Cutting Tools & Machine Accessories for the Manufacturing Industries such as Oil & Gas, Aero Space, etc... For more information on our Company, you can either email me or view our website www.torvalen.com.sg.

We are trying to revamp our image to give our consumers a fresh new perspective to our company, so we welcome all ideas.

Industry/Entity Type

Business

Requirements
Must have
• Must incorporate New Company Logo into the card as shown in Uploaded file.

```html
<!DOCTYPE html>
<html lang="en">
<head>
<meta charset="utf-8">
<title>Torvalen Tools — Business Card</title>
<link rel="stylesheet" href="https://fonts.googleapis.com/css2?family=Open+Sans:wght@400;600&display=swap">
<style>
  :root {
    --backdrop: #d9d9d9;
    --card-dark: #221e1c;
    --card-light: #ffffff;
    --brand-red: #8e1a22;
    --ink: #2b2b2b;
    --ink-soft: #555555;
    --on-dark: #f2f2f2;
  }
  * { box-sizing: border-box; margin: 0; padding: 0; }
  html, body {
    width: 1200px; height: 944px; overflow: hidden;
    background: var(--backdrop);
    font-family: "Open Sans", Arial, sans-serif;
  }
  .canvas { position: relative; width: 1200px; height: 944px; }

  .card {
    position: absolute;
    width: 580px; height: 350px;
    border-radius: 26px;
  }

  /* Front */
  .card--front {
    left: 70px; top: 80px;
    background: var(--card-dark);
    color: var(--on-dark);
  }
  .card--front .brand {
    position: absolute; left: 0; right: 0; top: 120px;
    display: flex; justify-content: center; align-items: center; gap: 16px;
  }
  .brand__dot {
    width: 30px; height: 30px; border-radius: 50%;
    background: var(--brand-red);
    flex: none;
  }
  .card--front .brand__name {
    font-size: 46px; font-weight: 600; letter-spacing: 1px;
    color: var(--on-dark);
  }
  .card--front .website {
    position: absolute; left: 0; right: 0; top: 250px;
    text-align: center; font-size: 17px; letter-spacing: 1px;
  }

  /* Back */
  .card--back {
    left: 550px; top: 500px;
    background: var(--card-light);
    color: var(--ink);
  }
  .card--back .brand {
    position: absolute; left: 36px; top: 48px;
    display: flex; align-items: center; gap: 10px;
  }
  .brand--small .brand__dot { width: 20px; height: 20px; }
  .card--back .brand__name {
    font-size: 28px; font-weight: 600; color: var(--brand-red);
  }
  .divider {
    position: absolute; left: 36px; right: 30px; top: 170px;
    height: 2px; background: var(--brand-red);
  }
  .person {
    position: absolute; right: 30px; top: 138px; text-align: right;
  }
  .person__name { font-size: 22px; color: var(--brand-red); line-height: 1.2; }
  .person__role { font-size: 14px; color: var(--ink-soft); margin-top: 8px; }

  .contacts {
    position: absolute; left: 36px; top: 206px;
    list-style: none; font-size: 16px; line-height: 24px;
  }
  .contacts li { display: flex; align-items: center; gap: 8px; }
  .contacts svg { width: 14px; height: 14px; fill: var(--brand-red); flex: none; }
  .address {
    position: absolute; right: 30px; top: 258px;
    font-size: 16px; line-height: 24px; text-align: right; font-style: normal;
  }
</style>
</head>
<body>
<main class="canvas">
  <section class="card card--front" aria-label="Card front">
    <div class="brand">
      <span class="brand__dot"></span>
      <span class="brand__name">TORVALEN TOOLS</span>
    </div>
    <p class="website">www.torvalentools.com</p>
  </section>

  <section class="card card--back" aria-label="Card back">
    <div class="brand brand--small">
      <span class="brand__dot"></span>
      <span class="brand__name">TORVALEN TOOLS</span>
    </div>

    <div class="person">
      <p class="person__name">Marcus Lendrey</p>
      <p class="person__role">director</p>
    </div>
    <div class="divider"></div>

    <ul class="contacts">
      <li>
        <svg viewBox="0 0 14 14" aria-hidden="true"><path d="M3 1l2.5 3-1.3 1.5a8 8 0 0 0 4.3 4.3L10 8.5l3 2.5-1.5 2C6 13 1 8 1 2.5z"/></svg>
        512-004-2200
      </li>
      <li>
        <svg viewBox="0 0 14 14" aria-hidden="true"><rect x="4" y="1" width="6" height="12" rx="1.2"/></svg>
        512-004-2201
      </li>
      <li>
        <svg viewBox="0 0 14 14" aria-hidden="true"><path d="M1 3h12v8H1z M1 3l6 5 6-5" /></svg>
        info@torvalentools.com
      </li>
      <li>
        <svg viewBox="0 0 14 14" aria-hidden="true"><circle cx="7" cy="7" r="6"/></svg>
        www.torvalentools.com
      </li>
    </ul>

    <address class="address">
      1480 Halden Park Rd.<br>
      Corvell, TX 78119
    </address>
  </section>
</main>
</body>
</html>
```